Herbal Apothecary Rebrand

I am in the process of merging two companies Fern Hollow Oils and Under Willow Apothecary. I am dissolving Fern Hollow Oils (FHO) and need to blend a few of the products into the Under Willow Apothecary (UWA) line. These blended products will take on a fresh new look. This is where I need some help. I have a few ideas but need some creative genius to bring them together.
The following products need to be merged and once a logo is agreed upon I will be working with this designer with further pay to create the following:
~ body oils (labels and packaging) **existing product shown in image A-1
~ plant bath medicines (labels and packaging) **a new product with the bottle and packaging shown in images attached
~ facial serum (labels and packaging - the packaging will be the same cardboard boxes used for the body oils) **existing product shown in
image A-2
~ teas (labeling) **a new product - packaging sample pics attached
~ as well as having the ability to carry over into the creation of 40 different essential oil containers. ** An idea I have is shown in image C-1.
Ideas...
I prefer distinct lines, square designs vs circular or curvy. I prefer clean and clear vs busy.
I like the layout shown in images A-1 & A-2 and could see moving forward with a very similar style without the indigenous logo. I would like to see what it looks like to have the UWA logo (building with trees) in place of the indigenous logo. ** I am open to reworking the UWA logo to make it a bit more vertical in size vs being quite small and horizontal. This could include revising or recreating the building and trees altogether.
I like the speckled background (shown in image B-1), it gives the sense that it is aged and goes with the Apothecary theme, however I'm not completely attached to it.
I like the off white labels that I currently have for the BODY OILS and the SERUM and I am leaning towards this as the colour for the new blended line. I would also be open to seeing a lighter version of the turquoise.
This is just an idea that I have however I am open to something completely new. What is important is that it blends nicely with the current line of products available at UWA (the entire line can be seen online). There is a good chance that I will be merging the products over to the new and improved design as we move through the older packaging.
Notes on Plant Bath labels:
**If working from the current layout of the Body Oil labels this can be used as an example to create a template
~ The top will have the new or reworked logo (with or without the company name depending on space available)
~ First line for each bottle will have a name eg: NETTLE + ROSE
~ Second line will be the purpose of the medicine eg: HEART OPENING
~ The next line will read: PLANT BATH
~Then space for a little blurb eg: BRINGING BALANCE TO THE EMOTIONAL AND ENERGETIC HEALTH OF THE HEART.
~ The size of the bottle will read 400 ML but in a vertical direction on the bottle
Notes on Tea labels:
The teas have not been created yet but I'm looking for some ideas that follow in the same design as the Plant Bath labels so the following can be used as an example:
~ Name; TULSI + ROSE
~ The purpose: ELEVATED HEART
~ The bottom will read: LOOSE TEA
~ Blurb about the benefits: A TRANSFORMATIONAL CREATION OF WARM NOTES WITH DEEP WOODY UNDERTONES. THIS ANYTIME TEA IS AS PLEASING IN THE HEALTH BENEFITS AS IT IS TO THE TASTE.
~ Include the size: 100g
**I maxed out in pictures so I wasn't able to add more inspiration pics but I also quite like the brook & meadow tea line (shows up in a google search) as its clean and clear. The difference being I won't be printing directly on the packaging, it will need to be a label.
Logo Text
I would like to see if we can incorporate the name UNDER WILLOW APOTHECARY however this might make it too busy. Perhaps smaller lettering for "under willow" and larger for "APOTHECARY". It also might be the case that adding this on the front makes things look too busy. I'm open to creative suggestions.

```html
<!DOCTYPE html>
<html lang="en">
<head>
<meta charset="utf-8">
<title>Under Willow Apothecary — Label System</title>
<link rel="stylesheet" href="https://fonts.googleapis.com/css2?family=Oswald:wght@300;400&family=Playfair+Display:wght@400;700&display=swap">
<style>
  :root{
    --ink:#7a2a1e;
    --paper:#f2f1ee;
    --teal:#5fc3b7;
    --kraft:#c69c6d;
    --stage:#d8d8d8;
    --white:#ffffff;
    --art-tone:#e9dcd8;
    --serif:"Playfair Display", Georgia, serif;
    --condensed:"Oswald", "Arial Narrow", sans-serif;
  }
  *{box-sizing:border-box;margin:0;padding:0}
  html,body{width:720px;height:1200px;overflow:hidden;background:var(--white)}
  .canvas{position:relative;width:720px;height:1200px;overflow:hidden}

  /* brand header */
  .brand{position:absolute;left:0;top:0;width:720px;height:682px;background:var(--white);
    display:flex;flex-direction:column;align-items:center;justify-content:center;color:var(--ink)}
  .brand__kicker{font-family:var(--serif);font-weight:700;font-size:26px;letter-spacing:5px;text-transform:uppercase;line-height:1}
  .brand__name{font-family:var(--serif);font-weight:400;font-size:72px;letter-spacing:2px;line-height:1;margin-top:14px}
  .brand__art{width:320px;height:110px;margin-top:30px;background:var(--art-tone)}

  /* label sheet */
  .sheet{position:absolute;left:0;top:682px;width:720px;height:518px;background:var(--stage)}
  .label{position:absolute;width:300px;height:218px;color:var(--ink);overflow:hidden}
  .label--teal{background:var(--teal)}
  .label--paper{background:var(--paper)}
  .label--kraft{background:var(--kraft)}

  .label__side{position:absolute;top:18px;height:184px;writing-mode:vertical-rl;transform:rotate(180deg);
    font-family:var(--condensed);font-weight:300;font-size:5px;line-height:1.3;text-transform:uppercase}
  .label__side b{font-weight:400}
  .label__use{left:14px;width:21px}
  .label__ingredients{left:39px;width:8px;white-space:nowrap}

  .label__kicker{position:absolute;left:85px;width:130px;top:19px;text-align:center;
    font-family:var(--serif);font-weight:700;font-size:8px;letter-spacing:1.5px;line-height:1;text-transform:uppercase}
  .label__name{position:absolute;left:85px;width:130px;top:29px;text-align:center;
    font-family:var(--serif);font-size:16px;letter-spacing:.4px;line-height:1}
  .label__art{position:absolute;left:98px;top:51px;width:104px;height:38px;background:var(--ink);opacity:.22}

  .label__info{position:absolute;left:85px;top:108px;width:130px}
  .row{border-bottom:1px solid var(--ink);font-family:var(--condensed);text-transform:uppercase;white-space:nowrap}
  .row--product{font-size:11px;font-weight:400;letter-spacing:.5px;height:19px;line-height:17px}
  .row--type{font-size:10.5px;font-weight:300;letter-spacing:.5px;height:19px;line-height:19px}
  .row--origin{font-size:7.5px;font-weight:300;letter-spacing:.3px;height:17px;line-height:20px;border-bottom-width:.6px}
  .row--blurb{display:flex;height:42px;border-bottom-width:.6px}
  .blurb{flex:1;font-size:7.8px;font-weight:300;line-height:1.25;letter-spacing:.2px;padding:5px 8px 0 0;white-space:normal}
  .size{width:26px;border-left:.6px solid var(--ink);margin:5px 0 4px;display:flex;align-items:center;justify-content:center}
  .size span{writing-mode:vertical-rl;transform:rotate(180deg);font-size:10.5px;font-weight:300;letter-spacing:.5px;text-transform:none}

  .label__panel{position:absolute;left:243px;top:19px;width:44px;height:184px;border:.6px solid var(--ink)}
  .label__web{position:absolute;right:5px;top:0;height:100%;writing-mode:vertical-rl;transform:rotate(180deg);
    text-align:center;font-family:var(--condensed);font-weight:300;font-size:6px;letter-spacing:.2px}
</style>
</head>
<body>
<main class="canvas">

  <header class="brand">
    <p class="brand__kicker">under willow</p>
    <h1 class="brand__name">APOTHECARY</h1>
    <div class="brand__art" role="img" aria-label="Hand-drawn cabin between pine trees illustration"></div>
  </header>

  <section class="sheet">

    <article class="label label--teal" style="left:45px;top:17px">
      <p class="label__side label__use"><b>Directions:</b> warm gently before use. Smooth over skin after a bath or shower. Work in slow strokes until fully absorbed. A few drops may be added to a warm bath.</p>
      <p class="label__side label__ingredients"><b>Ingredients:</b> jojoba oil, lavender, birch, bergamot, vetiver organic.</p>
      <p class="label__kicker">under willow</p>
      <p class="label__name">APOTHECARY</p>
      <div class="label__art" role="img" aria-label="Cabin and pine trees illustration"></div>
      <div class="label__info">
        <p class="row row--product">Lavender + Birch</p>
        <p class="row row--type">Soothing Body Oil</p>
        <p class="row row--origin">Organic Botanicals</p>
        <div class="row row--blurb"><p class="blurb">Calming and grounding for a restful sense of ease</p><div class="size"><span>100ML</span></div></div>
      </div>
      <div class="label__panel"><p class="label__web">underwillowapothecary.com</p></div>
    </article>

    <article class="label label--paper" style="left:374px;top:17px">
      <p class="label__side label__use"><b>Directions:</b> pour a generous cap into warm running water. Soak for twenty minutes and breathe slowly. Rinse lightly and rest after bathing.</p>
      <p class="label__side label__ingredients"><b>Ingredients:</b> epsom salt, yarrow, violet leaf, oat straw, calendula.</p>
      <p class="label__kicker">under willow</p>
      <p class="label__name">APOTHECARY</p>
      <div class="label__art" role="img" aria-label="Cabin and pine trees illustration"></div>
      <div class="label__info">
        <p class="row row--product">Yarrow + Violet</p>
        <p class="row row--type">Herbal Soak</p>
        <p class="row row--origin">Organic Botanicals</p>
        <div class="row row--blurb"><p class="blurb">Restoring calm to a weary body and a busy mind</p><div class="size"><span>400ML</span></div></div>
      </div>
      <div class="label__panel"><p class="label__web">underwillowapothecary.com</p></div>
    </article>

    <article class="label label--paper" style="left:45px;top:261px">
      <p class="label__side label__use"><b>To brew:</b> steep one heaped teaspoon in freshly boiled water for five minutes. Strain and enjoy hot, or pour over ice for a cool afternoon cup.</p>
      <p class="label__side label__ingredients"><b>Ingredients:</b> hibiscus, spearmint, lemon balm, rosehip, licorice root.</p>
      <p class="label__kicker">under willow</p>
      <p class="label__name">APOTHECARY</p>
      <div class="label__art" role="img" aria-label="Cabin and pine trees illustration"></div>
      <div class="label__info">
        <p class="row row--product">Hibiscus + Mint</p>
        <p class="row row--type">Herbal Infusion</p>
        <p class="row row--origin">Organic Botanicals</p>
        <div class="row row--blurb"><p class="blurb">A bright blend of tart notes with a cool and clean finish.</p><div class="size"><span>100g</span></div></div>
      </div>
      <div class="label__panel"><p class="label__web">underwillowapothecary.com</p></div>
    </article>

    <article class="label label--kraft" style="left:374px;top:261px">
      <p class="label__side label__use"><b>Directions:</b> pour a generous cap into warm running water. Soak for twenty minutes and breathe slowly. Rinse lightly and rest after bathing.</p>
      <p class="label__side label__ingredients"><b>Ingredients:</b> epsom salt, yarrow, violet leaf, oat straw, calendula.</p>
      <p class="label__kicker">under willow</p>
      <p class="label__name">APOTHECARY</p>
      <div class="label__art" role="img" aria-label="Cabin and pine trees illustration"></div>
      <div class="label__info">
        <p class="row row--product">Yarrow + Violet</p>
        <p class="row row--type">Herbal Soak</p>
        <p class="row row--origin">Organic Botanicals</p>
        <div class="row row--blurb"><p class="blurb">Restoring calm to a weary body and a busy mind</p><div class="size"><span>400ML</span></div></div>
      </div>
      <div class="label__panel"><p class="label__web">underwillowapothecary.com</p></div>
    </article>

  </section>
</main>
</body>
</html>
```